Executive Business Card for Healthcare Company [Need Today]

I need a business card design for a healthcare company. The only branding the company has thus far is a logo. The cards will be utilized by company executives. The design I envision will be vibrant and appealing but with a corporate feel. They shouldn't be too casual or playful. I would like to complete this project TODAY if possible.

Target Market(s)

Healthcare vendors, other executives in healthcare and pharmaceuticals

Industry/Entity Type

Pharmaceutical

Contact Information for Business Card

See attachment

Font styles to use
Serif
Sans Serif

Colors

Designer to choose colors to be used in the design.

```html
<!DOCTYPE html>
<html lang="en">
<head>
<meta charset="utf-8">
<title>Norvel Therapeutics – Executive Business Card</title>
<link rel="stylesheet" href="https://fonts.googleapis.com/css2?family=Quicksand:wght@500&family=Roboto:wght@300;400&display=swap">
<style>
  :root {
    --backdrop: #2e2f31;
    --card: #1b1c1e;
    --teal: #27c2a6;
    --aqua: #1fb3cc;
    --text-soft: #9aa3a8;
    --text-light: #c9d0d3;
  }
  * { margin: 0; padding: 0; box-sizing: border-box; }
  html, body { width: 800px; height: 1200px; overflow: hidden; }
  body {
    background: var(--backdrop);
    font-family: "Roboto", Arial, sans-serif;
    position: relative;
  }
  .card {
    position: absolute;
    left: 50px;
    width: 700px;
    height: 400px;
    background: var(--card);
    border-radius: 4px;
    overflow: hidden;
    box-shadow: 0 10px 30px rgba(0,0,0,0.35);
  }
  .card--front { top: 140px; }
  .card--back { top: 660px; }

  /* Front */
  .brand-lockup {
    position: absolute;
    left: 170px;
    top: 135px;
    display: flex;
    align-items: center;
    gap: 22px;
  }
  .brand-dot {
    width: 96px; height: 96px;
    border: 4px solid var(--teal);
    border-radius: 50%;
  }
  .brand-divider {
    width: 2px; height: 70px;
    background: var(--text-soft);
    opacity: 0.6;
  }
  .brand-name {
    font-family: "Quicksand", Arial, sans-serif;
    font-weight: 500;
    color: var(--teal);
    line-height: 1;
  }
  .brand-name__main { display: block; font-size: 58px; letter-spacing: 2px; }
  .brand-name__sub { display: block; font-size: 26px; margin-top: 4px; padding-left: 90px; }
  .web-address {
    position: absolute;
    left: 52px; bottom: 36px;
    font-size: 15px;
    letter-spacing: 2px;
    color: var(--text-soft);
  }

  /* Back */
  .back-ring { position: absolute; left: 0; top: 0; }
  .back-brand {
    position: absolute;
    left: 380px; top: 48px;
    font-family: "Quicksand", Arial, sans-serif;
    font-weight: 500;
    color: var(--teal);
    line-height: 1;
  }
  .back-brand__main { display: block; font-size: 44px; letter-spacing: 2px; }
  .back-brand__sub { display: block; font-size: 20px; margin-top: 2px; padding-left: 70px; }
  .contact {
    position: absolute;
    left: 390px; top: 158px;
  }
  .contact__name {
    font-size: 30px;
    font-weight: 400;
    color: var(--teal);
  }
  .contact__title {
    font-size: 13px;
    font-weight: 300;
    color: var(--text-soft);
    margin: 2px 0 14px;
  }
  .contact__list { list-style: none; }
  .contact__item {
    display: flex;
    align-items: center;
    gap: 10px;
    font-size: 14px;
    font-weight: 300;
    color: var(--text-light);
    line-height: 22px;
  }
  .contact__icon { width: 14px; height: 14px; flex: none; }
  .contact__item--plain { padding-left: 24px; }
</style>
</head>
<body>

<section class="card card--front" aria-label="Card front">
  <div class="brand-lockup">
    <div class="brand-dot"></div>
    <div class="brand-divider"></div>
    <div class="brand-name">
      <span class="brand-name__main">norvel</span>
      <span class="brand-name__sub">therapeutics</span>
    </div>
  </div>
  <p class="web-address">www.norveltx.com</p>
</section>

<section class="card card--back" aria-label="Card back">
  <svg class="back-ring" width="700" height="400" viewBox="0 0 700 400" aria-hidden="true">
    <defs>
      <linearGradient id="ringGradient" x1="0" y1="0" x2="1" y2="1">
        <stop offset="0" stop-color="#27c2a6"/>
        <stop offset="1" stop-color="#1fb3cc"/>
      </linearGradient>
    </defs>
    <circle cx="110" cy="215" r="205" fill="none" stroke="url(#ringGradient)" stroke-width="14"/>
  </svg>

  <div class="back-brand">
    <span class="back-brand__main">norvel</span>
    <span class="back-brand__sub">therapeutics</span>
  </div>

  <div class="contact">
    <h1 class="contact__name">Daniel Marsh</h1>
    <p class="contact__title">Senior Director of Marketing</p>
    <ul class="contact__list">
      <li class="contact__item">
        <svg class="contact__icon" viewBox="0 0 24 24" aria-hidden="true"><path fill="#27c2a6" d="M6.6 10.8a15 15 0 0 0 6.6 6.6l2.2-2.2a1 1 0 0 1 1-.25 11.4 11.4 0 0 0 3.6.57 1 1 0 0 1 1 1V20a1 1 0 0 1-1 1A17 17 0 0 1 3 4a1 1 0 0 1 1-1h3.5a1 1 0 0 1 1 1c0 1.25.2 2.45.57 3.6a1 1 0 0 1-.25 1z"/></svg>
        555-204-7716
      </li>
      <li class="contact__item">
        <svg class="contact__icon" viewBox="0 0 24 24" aria-hidden="true"><rect x="6" y="2" width="12" height="20" rx="2" fill="none" stroke="#27c2a6" stroke-width="2"/><circle cx="12" cy="18" r="1.3" fill="#27c2a6"/></svg>
        555-318-4402
      </li>
      <li class="contact__item">
        <svg class="contact__icon" viewBox="0 0 24 24" aria-hidden="true"><rect x="2" y="5" width="20" height="14" rx="1.5" fill="none" stroke="#27c2a6" stroke-width="2"/><path d="M2.5 6l9.5 7 9.5-7" fill="none" stroke="#27c2a6" stroke-width="2"/></svg>
        dmarsh@norveltx.com
      </li>
      <li class="contact__item">
        <svg class="contact__icon" viewBox="0 0 24 24" aria-hidden="true"><path fill="#27c2a6" d="M12 2a7 7 0 0 0-7 7c0 5 7 13 7 13s7-8 7-13a7 7 0 0 0-7-7zm0 9.5A2.5 2.5 0 1 1 12 6.5a2.5 2.5 0 0 1 0 5z"/></svg>
        118 W Hillcrest Avenue
      </li>
      <li class="contact__item contact__item--plain">Dalton, GA 30720</li>
    </ul>
  </div>
</section>

</body>
</html>
```